Disability provider requiring digital flyer to promote services

My company works within the Disability sector (KTAP registered provider), currently operating in Sydney, Australia.
I require a digital brochure which lists our services and gives potential customers a quick look into what we do with a single glance.
Undecided whether this digital flyer is to be single or double sided, happy to consult with an experienced designer in this regard.
I prefer minimalist designs (which may be an issue for someone trying to convey information, I'm not sure), and possibly someone who can work with out watercolor logo.
Services include:
-Supported Independent Living
-Specialist Disability Accommodation
-Individualised Living Options Stage 1 & 2
-Home Modifications
-Occupational Therapy
-Support Coordination Levels 1 & 2
-Short Term Accommodation - STA Respite
-Drop In Supports
-Community Access
Disability

```html
<!DOCTYPE html>
<html lang="en">
<head>
<meta charset="utf-8">
<title>Clearview Care – Disability Services Flyer</title>
<link href="https://fonts.googleapis.com/css2?family=Bebas+Neue&family=Barlow+Condensed:wght@400;500&family=Barlow+Semi+Condensed:wght@400;500&family=Montserrat:wght@800;900&family=Mulish:wght@500;600&display=swap" rel="stylesheet">
<style>
  :root{
    --green:#13773f;
    --green-dark:#1a4a2a;
    --green-deep:#0f3f22;
    --green-mid:#1b5a30;
    --lime:#8ab848;
    --olive:#76a040;
    --white:#ffffff;
    --purple:#6a2a7a;
    --ink:#1c2a20;
  }
  *{margin:0;padding:0;box-sizing:border-box}
  html,body{width:849px;height:1200px;overflow:hidden;background:#fff}
  .flyer{position:relative;width:849px;height:1200px;overflow:hidden;background:var(--green)}
  .backdrop{position:absolute;left:0;top:0}
  .brand-panel{position:absolute;left:76px;top:0;width:179px;height:178px;background:var(--green-dark);border-radius:0 0 52px 52px;display:flex;align-items:flex-end;justify-content:center;padding-bottom:46px}
  .brand-name{font-family:'Bebas Neue',sans-serif;color:var(--white);font-size:30px;letter-spacing:1px;text-align:center;line-height:1}
  .headline{position:absolute;left:73px;top:206px;font-family:'Bebas Neue',sans-serif;color:var(--white);font-size:50px;line-height:50px;letter-spacing:.3px;font-weight:400}
  .intro{position:absolute;left:75px;top:434px;font-family:'Barlow Semi Condensed',sans-serif;color:var(--white);font-size:20px;line-height:26px}
  .services-tab{position:absolute;left:0;top:680px;width:281px;height:51px;background:var(--green);border-radius:0 28px 0 0;padding:8px 0 0 24px;font-family:'Montserrat',sans-serif;font-weight:900;color:var(--white);font-size:29px;letter-spacing:.3px}
  .services{position:absolute;left:0;top:731px;width:849px}
  .service-row{position:relative;height:76px}
  .row-1{background:var(--lime)}
  .row-2{background:var(--olive)}
  .row-3{background:var(--green)}
  .row-4{background:var(--green-mid)}
  .row-5{background:var(--green-deep)}
  .service{position:absolute;top:0;height:76px;display:flex;align-items:center}
  .service.left{left:69px}
  .service.right{left:417px}
  .service-icon{width:74px;height:74px;border-radius:50%;border:3px solid var(--white);background:var(--green-dark);flex:none;display:flex;align-items:center;justify-content:center}
  .service-name{margin-left:10px;font-family:'Barlow Condensed',sans-serif;font-weight:400;color:var(--white);font-size:21px;line-height:21px}
  .footer{position:absolute;left:0;top:1111px;width:849px;height:86px;background:var(--white);border-bottom:3px solid var(--green-dark)}
  .talk-tab{position:absolute;z-index:2;right:0;top:1064px;width:308px;height:63px;background:var(--lime);border-radius:22px 0 0 0;font-family:'Montserrat',sans-serif;font-weight:900;color:var(--green-dark);font-size:35px;line-height:1;display:flex;align-items:center;justify-content:center;padding-left:10px}
  .badge{position:absolute;left:75px;top:13px;width:64px;height:64px;border-radius:50%;background:var(--purple)}
  .registered{position:absolute;left:149px;top:17px;font-family:'Mulish',sans-serif;font-weight:600;font-size:25px;line-height:27px}
  .registered .line-1{color:var(--purple);display:block}
  .registered .line-2{color:var(--lime);display:block}
  .contact{position:absolute;top:22px;font-family:'Mulish',sans-serif;font-weight:500;color:var(--ink);font-size:20px;line-height:27px;text-align:center}
  .contact.web{left:360px;width:220px}
  .contact.phone{left:620px;width:190px}
</style>
</head>
<body>
<main class="flyer">
  <svg class="backdrop" width="849" height="740" viewBox="0 0 849 740">
    <defs>
      <clipPath id="hero-circle"><circle cx="668" cy="250" r="268"/></clipPath>
      <linearGradient id="g-meal" x1="0" y1="0" x2="1" y2="1"><stop offset="0" stop-color="#c9d6de"/><stop offset=".5" stop-color="#8fb0cf"/><stop offset="1" stop-color="#d8cfe6"/></linearGradient>
      <linearGradient id="g-room" x1="0" y1="0" x2="1" y2="1"><stop offset="0" stop-color="#b9a78c"/><stop offset=".5" stop-color="#e4ddd1"/><stop offset="1" stop-color="#8a6a4a"/></linearGradient>
      <linearGradient id="g-p1" x1="0" y1="0" x2="1" y2="1"><stop offset="0" stop-color="#b7c8d6"/><stop offset="1" stop-color="#7a3a4a"/></linearGradient>
      <linearGradient id="g-p2" x1="0" y1="0" x2="1" y2="1"><stop offset="0" stop-color="#e07a30"/><stop offset="1" stop-color="#7a7a6a"/></linearGradient>
      <linearGradient id="g-p3" x1="0" y1="0" x2="1" y2="1"><stop offset="0" stop-color="#3a3f44"/><stop offset="1" stop-color="#c9b48a"/></linearGradient>
      <linearGradient id="g-p4" x1="0" y1="0" x2="1" y2="1"><stop offset="0" stop-color="#e8ecef"/><stop offset="1" stop-color="#b88a6a"/></linearGradient>
    </defs>
    <g role="img" aria-label="Young people drawing together at a table">
      <path d="M0,595 Q80,565 150,555 L158,730 L0,730 Z" fill="url(#g-p1)"/>
    </g>
    <g role="img" aria-label="Man in a wheelchair chatting with a support worker indoors">
      <path d="M155,545 Q280,542 390,560 L402,730 L168,730 Z" fill="url(#g-p2)"/>
    </g>
    <g role="img" aria-label="Man in a wheelchair on a vehicle lift">
      <path d="M398,565 Q520,590 640,620 L646,730 L418,730 Z" fill="url(#g-p3)"/>
    </g>
    <g role="img" aria-label="Hands holding a bathroom grab rail">
      <path d="M648,622 Q750,630 849,595 L849,730 L660,730 Z" fill="url(#g-p4)"/>
    </g>
    <path d="M392,345 C470,330 560,520 849,520 L849,570 C600,600 470,470 396,405 Z" fill="var(--lime)"/>
    <path d="M396,405 C470,470 600,600 849,570 L849,600 C620,640 470,520 396,405 Z" fill="#6a9a3c"/>
    <circle cx="668" cy="250" r="276" fill="var(--white)"/>
    <g clip-path="url(#hero-circle)">
      <g role="img" aria-label="Carer serving breakfast to a smiling older man">
        <rect x="390" y="-20" width="460" height="560" fill="url(#g-meal)"/>
      </g>
      <g role="img" aria-label="Accessible accommodation bedroom with desk">
        <polygon points="440,355 849,235 849,540 440,540" fill="url(#g-room)"/>
      </g>
      <polygon points="440,340 849,220 849,240 440,362" fill="var(--green-dark)"/>
    </g>
  </svg>

  <div class="brand-panel">
    <div class="brand-name">CLEARVIEW CARE</div>
  </div>

  <h1 class="headline">EMPOWERING<br>PEOPLE OF ALL<br>ABILITIES TO LIVE<br>AN INDEPENDENT LIFE</h1>
  <p class="intro">We provide inclusive and friendly<br>disability care services in Sydney, Australia</p>

  <h2 class="services-tab">OUR SERVICES</h2>

  <section class="services">
    <div class="service-row row-1">
      <div class="service left"><span class="service-icon"><svg width="36" height="40" viewBox="0 0 36 40" fill="none" stroke="#fff" stroke-width="2"><rect x="4" y="4" width="26" height="33" rx="2"/><path d="M9 13l3 3 5-6M9 22l3 3 5-6M20 14h6M20 23h6M9 31h17"/></svg></span><span class="service-name">Supported Independent Living</span></div>
      <div class="service right"><span class="service-icon"><svg width="40" height="40" viewBox="0 0 40 40" fill="none" stroke="#fff" stroke-width="2"><rect x="5" y="4" width="30" height="10" rx="2"/><path d="M4 20l16-6 16 6M8 19v16h24V19M16 35v-8h8v8"/></svg></span><span class="service-name">Specialist Disability Accommodation</span></div>
    </div>
    <div class="service-row row-2">
      <div class="service left"><span class="service-icon"><svg width="40" height="40" viewBox="0 0 40 40" fill="none" stroke="#fff" stroke-width="2"><path d="M4 20L18 7l14 13M8 17v17h12"/><circle cx="24" cy="25" r="7"/><path d="M29 30l6 6"/></svg></span><span class="service-name">Individualised Living Options<br>Stage 1 &amp; 2</span></div>
      <div class="service right"><span class="service-icon"><svg width="40" height="40" viewBox="0 0 40 40" fill="none" stroke="#fff" stroke-width="2"><circle cx="15" cy="6" r="3"/><path d="M15 11v10h9l4 9"/><circle cx="15" cy="26" r="8"/><path d="M4 36L36 24v12Z"/></svg></span><span class="service-name">Home Modifications</span></div>
    </div>
    <div class="service-row row-3">
      <div class="service left"><span class="service-icon"><svg width="40" height="40" viewBox="0 0 40 40" fill="none" stroke="#fff" stroke-width="2"><circle cx="12" cy="10" r="5"/><circle cx="29" cy="12" r="5"/><path d="M3 36V24a6 6 0 0 1 6-6h6a6 6 0 0 1 6 6v12M22 36V26a6 6 0 0 1 6-6h3a6 6 0 0 1 6 6v10"/></svg></span><span class="service-name">Occupational Therapy</span></div>
      <div class="service right"><span class="service-icon"><svg width="40" height="40" viewBox="0 0 40 40" fill="none" stroke="#fff" stroke-width="2"><circle cx="9" cy="10" r="4"/><circle cx="31" cy="10" r="4"/><rect x="14" y="6" width="12" height="9" rx="1"/><path d="M3 36V22a5 5 0 0 1 5-5h3M37 36V22a5 5 0 0 0-5-5h-3M10 26h20M20 26v10"/></svg></span><span class="service-name">Support Coordination Levels 1 &amp; 2</span></div>
    </div>
    <div class="service-row row-4">
      <div class="service left"><span class="service-icon"><svg width="40" height="40" viewBox="0 0 40 40" fill="none" stroke="#fff" stroke-width="2"><path d="M3 14L20 4l17 10M6 13v23h28V13"/><rect x="23" y="22" width="8" height="14"/><circle cx="13" cy="18" r="2"/><circle cx="13" cy="29" r="5"/></svg></span><span class="service-name">Short Term Accommodation -<br>STA Respite</span></div>
      <div class="service right"><span class="service-icon"><svg width="40" height="40" viewBox="0 0 40 40" fill="none" stroke="#fff" stroke-width="2"><circle cx="10" cy="7" r="4"/><path d="M5 36V16h10v20M10 22v14"/><path d="M17 30l4-6h9l6 4v4H17Z"/><circle cx="22" cy="33" r="2"/><circle cx="32" cy="33" r="2"/></svg></span><span class="service-name">Drop In Supports</span></div>
    </div>
    <div class="service-row row-5">
      <div class="service left"><span class="service-icon"><svg width="40" height="40" viewBox="0 0 40 40" fill="none" stroke="#fff" stroke-width="2"><circle cx="9" cy="14" r="4"/><circle cx="20" cy="12" r="4"/><circle cx="31" cy="14" r="4"/><path d="M3 30v-6a5 5 0 0 1 10 0M14 30v-8a6 6 0 0 1 12 0v8M27 30v-6a5 5 0 0 1 10 0M4 30h32M8 30v7M32 30v7"/></svg></span><span class="service-name">Community Access</span></div>
    </div>
  </section>

  <footer class="footer">
    <span class="badge"></span>
    <p class="registered"><span class="line-1">Registered</span><span class="line-2">KTAP Provider</span></p>
    <p class="contact web">www.clearviewcare.au<br>hello@clearviewcare.au</p>
    <p class="contact phone">+61 2 5550 1234<br>+61 3 5550 5678</p>
  </footer>

  <div class="talk-tab">TALK TO US</div>
</main>
</body>
</html>
```